Luxury Real Estate Website, Midwest, United States

We need web design services for a luxury website. We need IDX Integration with our MLS. We want this to be a very simple website with amazing graphics. We want it to link up with our MailChimp account in order to generate leads through a "More Information" Pop up on the main page. We want the main page to be covered with one large graphic that is a rolling slideshow of active listings of $400,000 and up from the IDX Integration. We need this website to give a very exclusive and sleek look. Lots of black is good... I will upload our logos in Black and Silver. We will also need an "About" page that we are going to call "Qeno Info". We want our graphics to be extremely impressive. Keep in mind, we are a company in the Midwest of the United States, and our real estate has a different look than homes in California or Florida. We need graphics that are realistic for the Midwest, yet still high-end.
Target Market(s)
Luxury Homeowners in the Midwest United States. The graphics needs to be pristine.
Industry/Entity Type
Real Estate
Coding
Coded - Design and coding required
Number of Pages Required
3 page
Requirements
Must have
- Large graphics with IDX Integration. The photos of real estate need to represent real estate that is common in the Midwest, United States. We also need MailChimp integration. We need a pop up that is titled "My Free Market Analysis" that makes them fill out a contact form asking for Full Name, Email Address, Phone Number and Address. This needs to be a pop up on the front page and will integrate with our MailChimp account. We also need a page called "About Qe No Home". And another page where clients can download informational PDFs. The main component needs to be a front page search engine connected with the IDX to access active listings from our MLS. I attached our logos and a sample front page of a website. I would love for ours to look similar.
Nice to have
- Lake House photos on midwest lakes are a plus.
Should not have
- Should not have clutter. This website needs to be clean, luxurious and exclusive.

```html
<!DOCTYPE html>
<html lang="en">
<head>
<meta charset="utf-8">
<title>Qeno Realty Group</title>
<link href="https://fonts.googleapis.com/css2?family=Jost:wght@400;500&family=Open+Sans:wght@400;600;700&display=swap" rel="stylesheet">
<style>
:root{
  --ink:#222;
  --text:#555;
  --muted:#777;
  --line:#333;
  --accent:#c9d9ea;
  --accent-ink:#1f2a36;
  --panel:#f6f6f6;
  --card:#f8f8f8;
  --footer:#c3c3c3;
  --bar:#222;
  --white:#fff;
  --hero-box:rgba(40,40,40,.72);
}
*{box-sizing:border-box;margin:0;padding:0}
html,body{width:1200px;height:2532px;overflow:hidden;background:var(--white)}
body{position:relative;font-family:"Open Sans",Arial,sans-serif;color:var(--text)}
.abs{position:absolute}
.heading{font-family:"Jost",Arial,sans-serif;font-weight:400;color:var(--ink);display:flex;align-items:center;gap:14px}
.heading::after{content:"";flex:1;height:1px;background:var(--line)}
.btn{display:inline-flex;align-items:center;justify-content:center;background:var(--accent);color:var(--accent-ink);font-weight:700;border-radius:2px}

/* header */
.site-header{left:0;top:0;width:1200px;height:79px;background:var(--white)}
.brand{left:118px;top:18px;display:flex;align-items:center;gap:12px;font-family:"Jost",sans-serif;font-weight:500;font-size:27px;color:var(--ink);letter-spacing:1px}
.brand-mark{width:14px;height:14px;background:var(--ink)}
.nav{right:110px;top:29px;display:flex;gap:31px;font-size:14px;color:var(--ink);align-items:center}
.nav .active{background:var(--ink);color:var(--white);padding:7px 15px;border-radius:4px;font-weight:600}

/* hero */
.hero{left:0;top:79px;width:1200px;height:529px;background:linear-gradient(180deg,#8fb0d4 0%,#5c7f48 25%,#3f5f33 48%,#58708c 62%,#3e5a86 100%)}
.hero-box{left:214px;top:250px;width:770px;height:258px;background:var(--hero-box);text-align:center;color:var(--white)}
.hero-title{margin-top:105px;font-family:"Jost",sans-serif;font-size:46px;font-weight:400;letter-spacing:.5px}
.hero-sub{margin:14px auto 0;width:590px;font-size:16px;line-height:21px}
.hero-arrow{top:340px}

/* info */
.info-photo{left:113px;top:636px;width:223px;height:117px;background:linear-gradient(120deg,#6b3d22,#b27448 45%,#7fa3b8 75%,#4f7a3c);box-shadow:0 2px 6px rgba(0,0,0,.35)}
.info-title{left:361px;top:638px;width:726px;font-size:23px}
.info-text{left:361px;top:674px;width:726px;font-size:12.5px;line-height:21px;color:var(--text)}
.info-btn{left:361px;top:727px;width:83px;height:24px;font-size:10px}

/* properties */
.props-title{left:113px;top:792px;width:974px;font-size:23px}
.grid{left:113px;top:861px;width:974px;display:grid;grid-template-columns:repeat(4,236px);column-gap:10px;row-gap:17px}
.card{background:var(--card)}
.card-photo{height:194px}
.card-body{height:76px;padding:14px 20px 0 20px;position:relative}
.card-name{font-family:"Jost",sans-serif;font-size:20px;color:var(--ink);line-height:22px}
.card-place{font-size:13px;color:var(--muted)}
.card-link{position:absolute;right:22px;top:26px}

/* about */
.about-title{left:113px;top:1474px;width:482px;font-size:23px}
.about-text{left:113px;top:1512px;width:482px;font-size:13px;line-height:21.5px;text-align:justify;color:var(--muted)}
.about-btn{left:113px;top:1615px;width:107px;height:33px;font-size:12.5px}
.about-photo{left:608px;top:1455px;width:479px;height:203px;background:linear-gradient(180deg,#9fc2e6 0%,#5f8e3e 35%,#3d6a2c 62%,#4b5a3a 80%,#3a4738 100%);box-shadow:0 2px 8px rgba(0,0,0,.35)}

/* testimonials */
.testimonials{left:0;top:1698px;width:1200px;height:365px;background:var(--panel)}
.testi-title{left:120px;top:1723px;width:962px;font-size:23px}
.quote{top:1811px;width:270px;height:199px;background:var(--white);border:1px solid #e4e4e4;text-align:center;padding:38px 26px 0}
.quote p{font-size:14.5px;line-height:21.5px;color:var(--ink)}
.quote .who{margin-top:12px;font-weight:700;font-size:14px}
.quote-badge{position:absolute;right:-1px;top:-23px;width:43px;height:43px;border-radius:50%;background:var(--accent);display:flex;align-items:center;justify-content:center;color:#2f4560;font-family:Georgia,serif;font-size:30px;font-weight:700;line-height:1;padding-top:12px}

/* partners */
.partner{top:2108px;width:160px;height:100px;border:1px solid #e4e4e4;display:flex;align-items:center;justify-content:center;font-family:"Open Sans",sans-serif;font-weight:700;font-size:20px;color:#b4b9c6}
.p-arrow{top:2141px}

/* footer */
.footer{left:0;top:2248px;width:1200px;height:232px;background:var(--footer)}
.f-title{font-family:"Jost",sans-serif;font-size:23px;color:var(--ink)}
.links{left:113px;top:2292px}
.links ul{list-style:none;margin-top:17px}
.links li{font-size:13px;color:var(--ink);line-height:21.5px;display:flex;align-items:center;gap:14px}
.links li::before{content:"›";font-size:17px;line-height:1}
.search{left:398px;top:2290px}
.field{width:330px;height:38px;background:var(--white);border:1px solid #bbb;margin-top:17px;display:flex;align-items:center;justify-content:space-between;padding:0 14px;font-size:11px;color:var(--ink)}
.newsletter{left:820px;top:2292px}
.newsletter .field{width:267px}
.sub-btn{margin-top:13px;width:125px;height:34px;font-size:16px}
.bottom-bar{left:0;top:2480px;width:1200px;height:52px;background:var(--bar);color:var(--white);font-size:12px}
.copy{left:0;width:1200px;top:18px;text-align:center}
.page-tag{right:55px;top:18px;font-weight:700;font-size:12px}
.to-top{right:126px;top:17px}
</style>
</head>
<body>

<header class="site-header abs">
  <div class="brand abs"><span class="brand-mark"></span>QENO REALTY GROUP</div>
  <nav class="nav abs">
    <span class="active">Home</span><span>Qeno Info</span><span>About Qe No Home</span><span>Downloads</span><span>Contact us</span>
  </nav>
</header>

<section class="hero abs" role="img" aria-label="Lakeside house among green trees reflected on a blue Midwest lake"></section>
<svg class="hero-arrow abs" style="left:110px" width="26" height="40" viewBox="0 0 26 40"><path d="M20 4 6 20l14 16" fill="none" stroke="#fff" stroke-width="5"/></svg>
<svg class="hero-arrow abs" style="left:1062px" width="26" height="40" viewBox="0 0 26 40"><path d="M6 4l14 16L6 36" fill="none" stroke="#fff" stroke-width="5"/></svg>
<div class="hero-box abs">
  <h1 class="hero-title">QENO HOME REALTY GROUP</h1>
  <p class="hero-sub">Vestibulum eros vel. Egestas et odio. Nec bibendum dolor pretium tortor sunt eros pretium hymenaeos. Cursus sit quisque.</p>
</div>

<div class="info-photo abs" role="img" aria-label="Covered wooden porch overlooking a wooded valley"></div>
<h2 class="info-title heading abs">Qe No Info</h2>
<p class="info-text abs">All the Lorem Ipsum generators on the Internet tend to repeat predefined chunks as necessary, making this the first true generator on the Internet.</p>
<span class="info-btn btn abs">Read more »</span>

<h2 class="props-title heading abs">Popular Properties</h2>
<div class="grid abs">
  <article class="card"><div class="card-photo" role="img" aria-label="Gabled house beside a pond with reflection" style="background:linear-gradient(180deg,#8fb3dc,#6c8a4a 55%,#4b6b8a)"></div><div class="card-body"><div class="card-name">Beautiful House</div><div class="card-place">Los Angels, 3654</div><svg class="card-link" width="20" height="20" viewBox="0 0 20 20"><g fill="none" stroke="#777" stroke-width="1.6"><path d="M8 12l4-4"/><rect x="1.5" y="9" width="9" height="5.5" rx="2.7" transform="rotate(-45 6 11.7)"/><rect x="9.5" y="5.5" width="9" height="5.5" rx="2.7" transform="rotate(-45 14 8.2)"/></g></svg></div></article>
  <article class="card"><div class="card-photo" role="img" aria-label="Large brick house with curved driveway" style="background:linear-gradient(180deg,#7aa6dc,#a89584 45%,#8c7e70 70%,#6f8a45)"></div><div class="card-body"><div class="card-name">Beautiful House</div><div class="card-place">Los Angels, 3654</div><svg class="card-link" width="20" height="20" viewBox="0 0 20 20"><g fill="none" stroke="#777" stroke-width="1.6"><path d="M8 12l4-4"/><rect x="1.5" y="9" width="9" height="5.5" rx="2.7" transform="rotate(-45 6 11.7)"/><rect x="9.5" y="5.5" width="9" height="5.5" rx="2.7" transform="rotate(-45 14 8.2)"/></g></svg></div></article>
  <article class="card"><div class="card-photo" role="img" aria-label="White house with porch and flower garden" style="background:linear-gradient(180deg,#5f8a3a,#c9c6bd 45%,#a7a49a 65%,#6c9a3c)"></div><div class="card-body"><div class="card-name">Beautiful House</div><div class="card-place">Los Angels, 3654</div><svg class="card-link" width="20" height="20" viewBox="0 0 20 20"><g fill="none" stroke="#777" stroke-width="1.6"><path d="M8 12l4-4"/><rect x="1.5" y="9" width="9" height="5.5" rx="2.7" transform="rotate(-45 6 11.7)"/><rect x="9.5" y="5.5" width="9" height="5.5" rx="2.7" transform="rotate(-45 14 8.2)"/></g></svg></div></article>
  <article class="card"><div class="card-photo" role="img" aria-label="Modern house at dusk under a pink sky" style="background:linear-gradient(180deg,#6f86c4,#d88aa8 35%,#3b3532 65%,#2d3a2a)"></div><div class="card-body"><div class="card-name">Beautiful House</div><div class="card-place">Los Angels, 3654</div><svg class="card-link" width="20" height="20" viewBox="0 0 20 20"><g fill="none" stroke="#777" stroke-width="1.6"><path d="M8 12l4-4"/><rect x="1.5" y="9" width="9" height="5.5" rx="2.7" transform="rotate(-45 6 11.7)"/><rect x="9.5" y="5.5" width="9" height="5.5" rx="2.7" transform="rotate(-45 14 8.2)"/></g></svg></div></article>
  <article class="card"><div class="card-photo" role="img" aria-label="Two-storey house with garage at dusk" style="background:linear-gradient(180deg,#c98a9a,#3d3d44 40%,#59524c 70%,#4a4a4a)"></div><div class="card-body"><div class="card-name">Beautiful House</div><div class="card-place">Los Angels, 3654</div><svg class="card-link" width="20" height="20" viewBox="0 0 20 20"><g fill="none" stroke="#777" stroke-width="1.6"><path d="M8 12l4-4"/><rect x="1.5" y="9" width="9" height="5.5" rx="2.7" transform="rotate(-45 6 11.7)"/><rect x="9.5" y="5.5" width="9" height="5.5" rx="2.7" transform="rotate(-45 14 8.2)"/></g></svg></div></article>
  <article class="card"><div class="card-photo" role="img" aria-label="Stone house with lawn and trees" style="background:linear-gradient(180deg,#4d6e32,#8d7a64 40%,#6f5f4e 70%,#5d8a36)"></div><div class="card-body"><div class="card-name">Beautiful House</div><div class="card-place">Los Angels, 3654</div><svg class="card-link" width="20" height="20" viewBox="0 0 20 20"><g fill="none" stroke="#777" stroke-width="1.6"><path d="M8 12l4-4"/><rect x="1.5" y="9" width="9" height="5.5" rx="2.7" transform="rotate(-45 6 11.7)"/><rect x="9.5" y="5.5" width="9" height="5.5" rx="2.7" transform="rotate(-45 14 8.2)"/></g></svg></div></article>
  <article class="card"><div class="card-photo" role="img" aria-label="Lit backyard with swimming pool at evening" style="background:linear-gradient(180deg,#3e5c9a,#b88a5a 40%,#27a7d8 70%,#1b8fc4)"></div><div class="card-body"><div class="card-name">Beautiful House</div><div class="card-place">Los Angels, 3654</div><svg class="card-link" width="20" height="20" viewBox="0 0 20 20"><g fill="none" stroke="#777" stroke-width="1.6"><path d="M8 12l4-4"/><rect x="1.5" y="9" width="9" height="5.5" rx="2.7" transform="rotate(-45 6 11.7)"/><rect x="9.5" y="5.5" width="9" height="5.5" rx="2.7" transform="rotate(-45 14 8.2)"/></g></svg></div></article>
  <article class="card"><div class="card-photo" role="img" aria-label="Row of stone cottages along a village lane" style="background:linear-gradient(180deg,#dfe6ee,#9a8a68 35%,#5f7a3a 65%,#7d7870)"></div><div class="card-body"><div class="card-name">Beautiful House</div><div class="card-place">Los Angels, 3654</div><svg class="card-link" width="20" height="20" viewBox="0 0 20 20"><g fill="none" stroke="#777" stroke-width="1.6"><path d="M8 12l4-4"/><rect x="1.5" y="9" width="9" height="5.5" rx="2.7" transform="rotate(-45 6 11.7)"/><rect x="9.5" y="5.5" width="9" height="5.5" rx="2.7" transform="rotate(-45 14 8.2)"/></g></svg></div></article>
</div>

<h2 class="about-title heading abs">About Qe No Home</h2>
<p class="about-text abs">Luctus amet sollicitudin nec aliquam in. Et suspendisse interdum non enim sodales. Purus morbi sit et curabitur tellus in metus curabitur. Aenean posuere suspendisse. Curabitur neque varius augue est diam. At adipiscing in sem felis praesent. Eros morbi nam fringilla ...</p>
<span class="about-btn btn abs">Read more »</span>
<div class="about-photo abs" role="img" aria-label="Lakeside cottages among tall green trees on a calm lake"></div>

<section class="testimonials abs"></section>
<h2 class="testi-title heading abs">Testimonials</h2>
<div class="quote abs" style="left:115px"><span class="quote-badge">”</span><p>“Eros morbi nam fringilla sed quis est sem nonummy. Laoreet felis in morbi nulla condimentum vitae pede pede faucibus blandit inter-dum nec”</p><p class="who">-Lara</p></div>
<div class="quote abs" style="left:466px"><span class="quote-badge">”</span><p>“Eros morbi nam fringilla sed quis est sem nonummy. Laoreet felis in morbi nulla condimentum vitae pede pede faucibus blandit inter-dum nec”</p><p class="who">-Jhon</p></div>
<div class="quote abs" style="left:815px"><span class="quote-badge">”</span><p>“Eros morbi nam fringilla sed quis est sem nonummy. Laoreet felis in morbi nulla condimentum vitae pede pede faucibus blandit inter-dum nec”</p><p class="who">-Ria</p></div>

<svg class="p-arrow abs" style="left:110px" width="22" height="34" viewBox="0 0 22 34"><path d="M17 3 5 17l12 14" fill="none" stroke="#ccc" stroke-width="4"/></svg>
<div class="partner abs" style="left:160px">Brightwell</div>
<div class="partner abs" style="left:407px">Norvane</div>
<div class="partner abs" style="left:655px">Tallis</div>
<div class="partner abs" style="left:879px">Fernlow</div>
<svg class="p-arrow abs" style="left:1066px" width="22" height="34" viewBox="0 0 22 34"><path d="M5 3l12 14L5 31" fill="none" stroke="#ccc" stroke-width="4"/></svg>

<footer class="footer abs"></footer>
<div class="links abs">
  <h3 class="f-title">Links</h3>
  <ul><li>Home</li><li>Qeno Info</li><li>About Qe No Home</li><li>Downloads</li><li>Contact us</li></ul>
</div>
<div class="search abs">
  <h3 class="f-title">Search</h3>
  <div class="field"><span>Search Now</span><svg width="16" height="16" viewBox="0 0 16 16"><circle cx="6.5" cy="6.5" r="4.8" fill="none" stroke="#555" stroke-width="2"/><path d="M10 10l4.5 4.5" stroke="#555" stroke-width="2.2"/></svg></div>
</div>
<div class="newsletter abs">
  <h3 class="f-title">Newsletter Subscribe</h3>
  <div class="field"><span>Email id</span><svg width="16" height="12" viewBox="0 0 16 12"><rect x="1" y="1" width="14" height="10" fill="none" stroke="#666" stroke-width="1.5"/><path d="M1 1l7 6 7-6" fill="none" stroke="#666" stroke-width="1.5"/></svg></div>
  <span class="sub-btn btn">Subscribe</span>
</div>

<div class="bottom-bar abs">
  <p class="copy abs">© copyrights 2018 &nbsp;|&nbsp; www.qenohome.example</p>
  <svg class="to-top abs" width="14" height="14" viewBox="0 0 14 14"><path d="M2 10l5-5 5 5" fill="none" stroke="#fff" stroke-width="2"/></svg>
  <span class="page-tag abs">M1</span>
</div>

</body>
</html>
```